Sunset Harbor Living Web Page

We need a web page design that has two intro pages - first being a 'home page', then a link to the second page that has the 'content tabs' and a 'call to action' (see below).

The business helps people that wish to retire to S.E.Asia (Thailand, Malaysia, Indonesia,The Philippines etc) - to enjoy the lifestyle and the remaining years of their lives. What attracts S.E.Asia to many people is the lower cost, the atmoshpere and beauty of the tropics and the vibrancy of the various countries.

People that are wishing to make the most of their retirement and are adventurous at a great bargain compared to the cost of their own countries will be interested.

We help them achieve this - visa, financials (tax, gov't payments etc), introduce them to the right people for property, clubs, retirement facilities, insurance and so forth.

Therefore we are providing an extremely wide ranging service and this site will provide broad but general information only - with a call to action to come and see us for more specific information and how we can help them specifically.

This site will be predominantly for travel and lifestyle, it will be linked with another financial services (financial planning) site later down the track.

The colour scheme is dark green and blue - as per the attached logo design. Photos and background just think lifestyle and S.E.Asia - beaches/mountains/water/recreational activities for retirees.

Target market is mostly those coming up to retirement to those that are already retired. But we also expect to have some interest with younger people that would like to find out more and plan for the future. So a broad age group but I would say mostly 40-70 yrs old.

On the first (Home) page we would like our company name 'Sunset Harbor Living', our logo (which will be on all pages) and a statement such as: “Imagine a retirement where your dreams are brought to life, and you have never felt more alive. Let us show you how”. Then a link to the second page.

We would like an uncluttered site. On the second (contents) page the tabs would be:

- Visa
- Property
- Financials
- Travel
- Insurance & Healthcare
- Medical Tourism
- Cost of living
- Weekly Blogs and articles
- Sunset Harbor Living story

We would also like a call to action on the second page - asking them to leave their contact details if they wish to learn more or sign up to our weekly newsletter/blog.

We are open to suggestions and your imaginations.

Thank you
Malcolm

Font styles to use
Serif
Script

Colors
0255a3
3377b5
00a990
9bcb3c
abd036
33b8a4
85abd2
cadf82
86cfc6

Requirements
Must have
• I have been asked by the web designer to receive a 'Web Font' so that we can 'get off of Zentrofy'. Hope that makes sense.

```html
<!DOCTYPE html>
<html lang="en">
<head>
<meta charset="utf-8">
<title>Sunset Harbor Living</title>
<link href="https://fonts.googleapis.com/css2?family=Ruda:wght@400;700;900&family=Open+Sans:wght@400;600&display=swap" rel="stylesheet">
<style>
  :root {
    --blue-dark: #0255a3;
    --blue: #3377b5;
    --teal: #00a990;
    --green: #00ad4f;
    --lime: #9bcb3c;
    --lime-btn: #abd036;
    --backdrop: #e4ddd0;
    --white: #ffffff;
    --panel: #f1f1f1;
    --text-muted: #b5b5b5;
    --heading-font: "Ruda", sans-serif;
    --body-font: "Open Sans", sans-serif;
  }
  * { box-sizing: border-box; margin: 0; padding: 0; }
  html, body { width: 1200px; height: 2894px; overflow: hidden; }
  body { background: var(--backdrop); font-family: var(--body-font); position: relative; }
  .page {
    position: absolute; left: 133px; top: 69px; width: 934px; height: 2589px;
    background: var(--white); box-shadow: 0 2px 6px rgba(0,0,0,.15);
  }
  .abs { position: absolute; }
  .brand {
    left: 0; width: 934px; top: 14px; height: 68px;
    display: flex; align-items: center; justify-content: center; gap: 10px;
  }
  .brand-dot { width: 30px; height: 30px; border-radius: 50%; background: var(--green); }
  .brand-name { font-family: var(--heading-font); font-weight: 900; font-size: 22px; color: var(--blue-dark); }
  .main-nav {
    left: 12px; top: 97px; width: 910px; height: 58px; background: var(--teal);
    display: flex; align-items: center;
  }
  .main-nav a {
    color: var(--white); text-decoration: none; font-family: var(--heading-font);
    font-size: 9.5px; text-transform: uppercase; padding: 0 9px; height: 58px; line-height: 58px; white-space: nowrap;
  }
  .main-nav a.active { background: var(--blue-dark); padding: 0 24px 0 24px; }
  .hero {
    left: 12px; top: 155px; width: 910px; height: 397px;
    background: linear-gradient(180deg, #3a8fd8 0%, #8cc4ee 30%, #5fb7a0 52%, #1fb3c4 68%, #6fd0d6 80%, #e9e2cf 92%, #f1ead8 100%);
  }
  .hero-card {
    left: 35px; top: 220px; width: 260px; height: 268px; background: var(--lime); padding: 34px 24px;
    color: var(--white);
  }
  .hero-brand { display: flex; align-items: center; gap: 8px; margin-bottom: 26px; }
  .hero-brand .dot { width: 22px; height: 22px; border-radius: 50%; background: var(--white); }
  .hero-brand span { font-family: var(--heading-font); font-weight: 900; font-size: 14px; }
  .hero-card p { font-family: var(--heading-font); font-size: 14px; line-height: 24px; }
  .hero-dots { left: 0; width: 934px; top: 518px; display: flex; justify-content: center; gap: 12px; }
  .hero-dots i { width: 9px; height: 9px; border-radius: 50%; background: #e8e8e8; display: block; }
  .hero-dots i.on { background: var(--lime); }
  .section-title {
    left: 0; width: 934px; text-align: center; font-family: var(--heading-font);
    font-weight: 700; font-size: 27px; color: var(--blue-dark); text-transform: uppercase;
  }
  .service { width: 288px; height: 242px; }
  .service .photo { width: 288px; height: 172px; }
  .service .label {
    height: 70px; background: var(--green); color: var(--white); text-align: center;
    font-family: var(--heading-font); font-size: 19px; line-height: 70px;
  }
  .cost-photo { left: 12px; top: 1247px; width: 443px; height: 258px; border: 4px solid #e4e4e4;
    background: linear-gradient(135deg, #d9c59a, #e6d2a8 40%, #bcd0c6 70%, #a8b9b3); }
  .cost-title { left: 479px; top: 1243px; font-family: var(--heading-font); font-weight: 700; font-size: 26px; color: var(--blue-dark); }
  .cost-text { left: 479px; top: 1300px; width: 443px; font-size: 11px; line-height: 19px; color: var(--text-muted); }
  .cost-text p + p { margin-top: 12px; }
  .btn-blue {
    left: 479px; top: 1468px; width: 106px; height: 35px; background: var(--blue-dark); color: var(--white);
    font-size: 11px; text-align: center; line-height: 35px; font-weight: 600;
  }
  .arrow { top: 1588px; }
  .blog { width: 288px; height: 468px; background: var(--panel); top: 1658px; }
  .blog .photo { height: 202px; }
  .blog h3 { margin: 22px 24px 0; font-family: var(--heading-font); font-weight: 400; font-size: 19px; line-height: 24px; color: var(--teal); }
  .blog p { margin: 18px 24px 0; font-size: 10.5px; line-height: 18px; color: var(--text-muted); }
  .btn-green { margin: 16px 24px 0; width: 87px; height: 31px; background: var(--green); color: var(--white);
    font-size: 10px; text-align: center; line-height: 31px; font-weight: 600; }
  .story { width: 288px; top: 2238px; }
  .story .photo { height: 197px; position: relative; }
  .play { position: absolute; left: 122px; top: 77px; }
  .story p { margin-top: 24px; font-family: var(--heading-font); font-size: 15px; line-height: 22px; color: var(--teal); }
  .pager { left: 0; width: 934px; top: 2532px; display: flex; justify-content: center; gap: 18px; }
  .signup-title { left: 0; width: 1200px; top: 2722px; text-align: center; font-family: var(--heading-font);
    font-weight: 700; font-size: 18px; color: var(--blue-dark); text-transform: uppercase; }
  .signup-input { left: 305px; top: 2762px; width: 457px; height: 33px; background: var(--white);
    font-size: 10px; color: #c8c8c8; padding-left: 12px; line-height: 33px; }
  .signup-btn { left: 774px; top: 2762px; width: 119px; height: 33px; background: var(--lime-btn);
    color: var(--white); font-size: 10px; text-align: center; line-height: 33px; font-weight: 600; }
  .footer-note { left: 0; width: 1200px; top: 2812px; text-align: center; font-size: 9px; color: #9c978c; }
</style>
</head>
<body>
<div class="page">
  <div class="abs brand"><span class="brand-dot"></span><span class="brand-name">Sunset Harbor Living</span></div>

  <nav class="abs main-nav">
    <a class="active" href="#">Home</a>
    <a href="#">Visa</a>
    <a href="#">Property</a>
    <a href="#">Financials</a>
    <a href="#">Travel</a>
    <a href="#">Insurance &amp; Healthcare</a>
    <a href="#">Medical Tourism</a>
    <a href="#">Cost of Living</a>
    <a href="#">Weekly Blogs and Articles</a>
    <a href="#">Sunset Harbor Story</a>
    <a href="#">Contact Us</a>
  </nav>

  <div class="abs hero" role="img" aria-label="Tropical beach with limestone cliffs, turquoise sea and a longtail boat"></div>
  <div class="abs hero-card">
    <div class="hero-brand"><span class="dot"></span><span>Sunset Harbor Living</span></div>
    <p>Imagine a retirement where your dreams are brought to life, and you have never felt more alive. Let us show you how</p>
  </div>
  <div class="abs hero-dots"><i class="on"></i><i></i><i></i><i></i></div>

  <h2 class="abs section-title" style="top:596px">What We Provide</h2>

  <div class="abs service" style="left:12px;top:654px">
    <div class="photo" role="img" aria-label="Hands holding a passport" style="background:linear-gradient(135deg,#dfe3e8,#9fb4cc 55%,#e9ddd2)"></div>
    <div class="label">Visa</div>
  </div>
  <div class="abs service" style="left:324px;top:654px">
    <div class="photo" role="img" aria-label="Modern glass apartment tower beside trees" style="background:linear-gradient(135deg,#4b86c4,#8fb6d8 50%,#5f9a45)"></div>
    <div class="label">Property</div>
  </div>
  <div class="abs service" style="left:635px;top:654px">
    <div class="photo" role="img" aria-label="Businessman using a tablet in the city" style="background:linear-gradient(135deg,#8e98a4,#cdd4da 50%,#4a5868)"></div>
    <div class="label">Financials</div>
  </div>
  <div class="abs service" style="left:12px;top:924px">
    <div class="photo" role="img" aria-label="Medical tourism concept with healthcare icons" style="background:linear-gradient(135deg,#cfe6f2,#3ea6d9 50%,#d9ecf4)"></div>
    <div class="label">Medical Tourism</div>
  </div>
  <div class="abs service" style="left:324px;top:924px">
    <div class="photo" role="img" aria-label="Traveller in a boat watching a golden sunset over water" style="background:linear-gradient(180deg,#f2d48a,#c8a058 50%,#3c4a52)"></div>
    <div class="label">Travel</div>
  </div>
  <div class="abs service" style="left:635px;top:924px">
    <div class="photo" role="img" aria-label="Doctor with a patient and stethoscope" style="background:linear-gradient(135deg,#e5eef2,#a9c6d6 50%,#f2f4f5)"></div>
    <div class="label">Insurance &amp; Healthcare</div>
  </div>

  <div class="abs cost-photo" role="img" aria-label="Globe showing Southeast Asia"></div>
  <h2 class="abs cost-title">COST OF LIVING</h2>
  <div class="abs cost-text">
    <p>Lorem ipsum dolor sit amet, consectetur adipiscing elit, sed do eiusmod tempor incididunt ut labore et dolore magna aliqua. Ut enim ad minim veniam, quis nostrud exercitation ullamco laboris nisi ut aliquip ex ea commodo consequat. Duis aute irure dolor in reprehenderit in voluptate velit esse cillum dolore eu fugiat nulla pariatur.</p>
    <p>Lorem ipsum dolor sit amet, consectetur adipiscing elit, sed do eiusmod tempor incididunt ut labore et dolore magna aliqua. Ut enim ad minim veniam.</p>
  </div>
  <div class="abs btn-blue">Learn More</div>

  <h2 class="abs section-title" style="top:1584px">Weekly Blogs and Articles</h2>
  <svg class="abs arrow" style="left:12px" width="14" height="24" viewBox="0 0 14 24"><path d="M11 3 L3 12 L11 21" fill="none" stroke="#c4c4c4" stroke-width="2"/></svg>
  <svg class="abs arrow" style="left:908px" width="14" height="24" viewBox="0 0 14 24"><path d="M3 3 L11 12 L3 21" fill="none" stroke="#c4c4c4" stroke-width="2"/></svg>

  <article class="abs blog" style="left:12px">
    <div class="photo" role="img" aria-label="Elephant ride before an ancient temple" style="background:linear-gradient(180deg,#8fb3d0,#c89a5c 55%,#5e7a3a)"></div>
    <h3>Sed ut perspiciatis unde omnis iste natus error sit voluptatem</h3>
    <p>Lorem ipsum dolor sit amet, consectetur adipiscing elit, sed do eiusmod tempor incididunt ut labore et dolore magna aliqua. Ut enim ad minim veniam</p>
    <div class="btn-green">Read More</div>
  </article>
  <article class="abs blog" style="left:324px">
    <div class="photo" role="img" aria-label="River winding through karst mountains" style="background:linear-gradient(180deg,#6f8fb8,#a9c3d8 35%,#5c8a52 70%,#3f6a78)"></div>
    <h3>Sed ut perspiciatis unde omnis iste natus error sit voluptatem</h3>
    <p>Lorem ipsum dolor sit amet, consectetur adipiscing elit, sed do eiusmod tempor incididunt ut labore et dolore magna aliqua. Ut enim ad minim veniam</p>
    <div class="btn-green">Read More</div>
  </article>
  <article class="abs blog" style="left:635px">
    <div class="photo" role="img" aria-label="Great Wall across green hills at sunrise" style="background:linear-gradient(180deg,#f0c66a,#b89045 40%,#4e6a2e)"></div>
    <h3>Sed ut perspiciatis unde omnis iste natus error sit voluptatem</h3>
    <p>Lorem ipsum dolor sit amet, consectetur adipiscing elit, sed do eiusmod tempor incididunt ut labore et dolore magna aliqua. Ut enim ad minim veniam</p>
    <div class="btn-green">Read More</div>
  </article>

  <h2 class="abs section-title" style="top:2168px">Sunset Harbor Living Story</h2>

  <div class="abs story" style="left:12px">
    <div class="photo" role="img" aria-label="Video testimonial from a smiling woman" style="background:linear-gradient(135deg,#e8e2d8,#c9b3a0 50%,#8a5aa6)">
      <svg class="play" width="44" height="44" viewBox="0 0 44 44"><circle cx="22" cy="22" r="20" fill="none" stroke="#fff" stroke-width="2"/><path d="M17 13 L31 22 L17 31 Z" fill="#fff"/></svg>
    </div>
    <p>Sed ut perspiciatis unde omnis iste natus error sit voluptatem</p>
  </div>
  <div class="abs story" style="left:324px">
    <div class="photo" role="img" aria-label="Video testimonial from a smiling man" style="background:linear-gradient(135deg,#6b8a4e,#c9a88a 50%,#4a4a4a)">
      <svg class="play" width="44" height="44" viewBox="0 0 44 44"><circle cx="22" cy="22" r="20" fill="none" stroke="#fff" stroke-width="2"/><path d="M17 13 L31 22 L17 31 Z" fill="#fff"/></svg>
    </div>
    <p>Sed ut perspiciatis unde omnis iste natus error sit voluptatem</p>
  </div>
  <div class="abs story" style="left:635px">
    <div class="photo" role="img" aria-label="Video testimonial from a man by a brick wall" style="background:linear-gradient(135deg,#d8d0c8,#b06a52 55%,#8a3f2e)">
      <svg class="play" width="44" height="44" viewBox="0 0 44 44"><circle cx="22" cy="22" r="20" fill="none" stroke="#fff" stroke-width="2"/><path d="M17 13 L31 22 L17 31 Z" fill="#fff"/></svg>
    </div>
    <p>Sed ut perspiciatis unde omnis iste natus error sit voluptatem</p>
  </div>

  <div class="abs pager">
    <svg width="30" height="30" viewBox="0 0 30 30"><circle cx="15" cy="15" r="15" fill="#00ad4f"/><path d="M17 9 L11 15 L17 21" fill="none" stroke="#fff" stroke-width="3"/></svg>
    <svg width="30" height="30" viewBox="0 0 30 30"><circle cx="15" cy="15" r="15" fill="#00ad4f"/><path d="M13 9 L19 15 L13 21" fill="none" stroke="#fff" stroke-width="3"/></svg>
  </div>
</div>

<h2 class="abs signup-title">Sign Up to Our Weekly Newsletter/Blog</h2>
<div class="abs signup-input">Enter your E-mail address</div>
<div class="abs signup-btn">SUBSCRIBE</div>
<p class="abs footer-note">© 2016 COMPANY NAME | ALL RIGHTS RESERVED</p>
</body>
</html>
```